Summit Builders Web Site / Business Cards

Construction Company that specializes in Water and Fire Damage, Residential ReModels, Landscaping and Building ADU (Accessory Dwelling Unit)

Growing and changing families often need additional space, and a remodeling project can often provide that. Adding a new area, or repurposing an existing one can satisfy this requirement.

Other times, homeowners want to update the look in their kitchen or bathroom with more than just a change of cabinetry or vanity doors and drawers. Whatever your needs are, Summit Builders has skilled workers who are bonded and insured, and ready to make your dreams and visions a reality.

Target Market(s)

Home Owners

Industry/Entity Type

Construction Company

Contact Information for Business Card

Center Logo with our information on the corners

Back side to be Logo Only
Contact Info
CSLB License # 2418596
info@summitbuildersca.example
www.summitbuildersca.example

Coding

Coded - Design and coding required

Number of Pages Required

5+ page

Font styles to use
Serif
Sans Serif

Requirements
Must have
• Using our Logo Colors
Home
About Us
Services
Projects / Portfolio
Contact Us
Nice to have
• Colors matching our Logo
Should not have
• Black because it doesnt match our logo

```html
<!DOCTYPE html>
<html lang="en">
<head>
<meta charset="utf-8">
<title>Summit Builders</title>
<link href="https://fonts.googleapis.com/css2?family=Montserrat:wght@400;500;600;700;800&display=swap" rel="stylesheet">
<style>
:root{
  --orange:#fb6a0c;
  --ink:#1b1b1b;
  --text:#555;
  --field:#ececec;
  --page:#ffffff;
  --panel:#f3f3f3;
  --dark:#222427;
}
*{box-sizing:border-box;margin:0;padding:0}
html,body{width:1200px;height:3984px;overflow:hidden}
body{position:relative;background:var(--page);font-family:'Montserrat',Arial,sans-serif;color:var(--ink)}
.abs{position:absolute}
.center{text-align:center}

/* header */
.topbar{left:394px;top:0;width:806px;height:36px}
.topbar-text{top:0;height:36px;display:flex;align-items:center;color:#fff;font-size:13px}
.brand{left:162px;top:40px;display:flex;align-items:center;gap:10px}
.brand-mark{width:26px;height:26px;background:var(--orange)}
.brand-name{font-size:25px;font-weight:800;color:var(--ink);letter-spacing:.5px}
.nav{top:68px;right:164px;display:flex;gap:48px;font-size:12px;font-weight:700}
.nav a{color:var(--ink);text-decoration:none}
.nav a.active{color:var(--orange)}

/* hero */
.hero{left:0;top:112px;width:1200px;height:638px;background:linear-gradient(100deg,#5f7b8a 0%,#8ea2aa 30%,#b9a36a 40%,#4c5b66 55%,#2d3640 100%)}
.hero-shade{left:0;top:112px}
.hero-title{right:164px;top:318px;text-align:right;color:#fff;font-size:50px;font-weight:800;line-height:84px}
.hero-sub{right:164px;top:480px;color:var(--orange);font-size:31px;font-weight:500;line-height:40px}
.quote-tri{left:0;top:572px}
.quote-tri-text{left:490px;top:655px;width:160px;color:#fff;font-weight:700;font-size:24px;line-height:32px}

/* who we are */
.h2{font-size:37px;font-weight:800;color:var(--ink)}
.who-title{left:162px;top:832px}
.who-sub{left:162px;top:880px;color:var(--orange);font-size:20px;font-weight:400}
.para{font-size:11.5px;line-height:20px;color:var(--text)}
.who-para{left:162px;top:922px;width:520px;font-size:10.8px}
.value{width:150px;text-align:center;font-size:11px;font-weight:700;line-height:22px;color:var(--ink)}
.value-dot{width:62px;height:62px;border-radius:50%;background:var(--orange);margin:0 auto 12px;display:flex;align-items:center;justify-content:center}

.quote-card{left:739px;top:827px;width:298px;height:348px;background:#fff;box-shadow:0 4px 18px rgba(0,0,0,.08)}
.quote-card-title{left:739px;top:848px;width:298px;color:#fff;font-size:27px;font-weight:700}
.field{background:var(--field);font-size:10.5px;color:#777;padding:10px 9px}
.btn{background:var(--dark);color:#fff;font-size:12px;font-weight:700;display:flex;align-items:center;justify-content:center}

.mine{left:0;top:1100px;width:1200px;height:502px;background:linear-gradient(180deg,#ffffff 0%,#ffffff 6%,#c9c4be 16%,#9c8f83 42%,#7d6b5c 75%,#6a584a 100%)}

/* stats */
.stats{left:0;top:1602px;width:1200px;height:150px;background:var(--orange)}
.stat{top:1628px;width:220px;text-align:center;color:#fff}
.stat-num{font-size:56px;font-weight:800;line-height:66px}
.stat-label{font-size:11.5px;font-weight:600}

/* services */
.card{top:1943px;width:195px;height:283px;background:var(--panel)}
.card-photo{height:130px;position:relative;overflow:hidden}
.card-title{font-size:13.5px;font-weight:700;padding:18px 13px 8px}
.card-text{font-size:10.5px;line-height:21px;color:#888;padding:0 13px}

/* projects */
.projects{left:0;top:2311px;width:1200px;height:657px;background:var(--panel)}
.tile{position:absolute}

/* testimonial */
.testimonial{left:0;top:2968px;width:1200px;height:186px;background:linear-gradient(90deg,#2a2a2a,#1c1d1f 60%,#2a2b2d)}
.avatar{left:161px;top:3010px;width:112px;height:112px;border-radius:50%;background:linear-gradient(160deg,#e9e3dc,#b9a593)}
.badge{left:240px;top:3000px;width:32px;height:32px;border-radius:50%;background:var(--orange);color:#fff;font-weight:800;font-size:20px;text-align:center;line-height:36px}
.test-text{left:294px;top:3009px;width:740px;color:#ddd;font-size:11.5px;line-height:22px}
.test-name{left:294px;top:3066px;color:#fff;font-size:13px}
.test-name b{color:var(--orange)}
.dot{top:3102px;width:11px;height:11px;border-radius:50%;border:1.5px solid var(--orange)}

/* footer */
.footer{left:0;top:3735px;width:1200px;height:249px;background:var(--orange)}
.footer-brand{left:0;top:3700px;width:1200px;display:flex;justify-content:center;align-items:center;gap:10px}
.footer-brand .brand-name{font-size:30px}
.ficon{width:56px;height:56px;border-radius:50%;background:#fff;display:flex;align-items:center;justify-content:center}
.finfo{color:#fff;font-size:11px;line-height:22px}
.finfo b{font-size:12.5px}
.social{top:3898px;width:12px;height:12px;border-radius:50%;background:#fff}
.copy{left:0;top:3925px;width:1200px;text-align:center;color:#fff;font-size:10px}
</style>
</head>
<body>

<!-- Header -->
<svg class="abs topbar" width="806" height="36" viewBox="0 0 806 36"><polygon points="14,0 806,0 806,36 0,36" fill="var(--orange)"/></svg>
<div class="abs topbar-text" style="left:424px;font-weight:700">ISO 9001:2017</div>
<div class="abs topbar-text" style="left:576px">
  <svg width="14" height="10" viewBox="0 0 14 10" style="margin-right:7px"><rect x=".5" y=".5" width="13" height="9" fill="none" stroke="#fff"/><polyline points=".5,.5 7,6 13.5,.5" fill="none" stroke="#fff"/></svg>hello@summitbuildersca.example</div>
<div class="abs topbar-text" style="left:842px">Call us&nbsp;
  <svg width="16" height="16" viewBox="0 0 24 24" style="margin:0 4px"><path fill="#fff" d="M6.6 10.8a15 15 0 006.6 6.6l2.2-2.2a1 1 0 011-.25 11.4 11.4 0 003.6.6 1 1 0 011 1V20a1 1 0 01-1 1A17 17 0 013 4a1 1 0 011-1h3.5a1 1 0 011 1c0 1.25.2 2.45.6 3.6a1 1 0 01-.25 1z"/></svg><b>+1 555 014 2290</b></div>

<div class="abs brand"><span class="brand-mark"></span><span class="brand-name">Summit Builders</span></div>

<nav class="abs nav">
  <a class="active" href="#">HOME</a><a href="#">ABOUT</a><a href="#">SERVICES</a><a href="#">PROJECTS</a><a href="#">CONTACT</a>
</nav>

<!-- Hero -->
<div class="abs hero" role="img" aria-label="Photo of a modern house entrance at dusk with a lit doorway and garage"></div>
<svg class="abs hero-shade" width="1200" height="638" viewBox="0 0 1200 638"><polygon points="860,0 1200,0 1200,638 480,638" fill="rgba(20,24,30,.55)"/></svg>
<div class="abs hero-title">THE BEST<br>CHOOSE US</div>
<div class="abs hero-sub">Because We Deliver</div>
<svg class="abs quote-tri" width="1200" height="178" viewBox="0 0 1200 178"><polygon points="569,0 690,178 448,178" fill="var(--orange)"/></svg>
<div class="abs quote-tri-text center">GET A<br>QUOTE</div>

<!-- Who we are (background band first so text sits above it) -->
<div class="abs mine" role="img" aria-label="Photo of a large bucket-wheel excavator in an open-pit quarry"></div>

<h2 class="abs h2 who-title">WHO WE ARE</h2>
<div class="abs who-sub">WE DELIVER LANDMARK PROJECTS</div>
<p class="abs para who-para">We are rethoric question ran over her cheek When she reached the first hills of the Italic Mountains, she had a last view back on the skyline of her hometown Bookmarksgrove, the headline of Alphabet Village and the subline of her own road, the Line Lane.</p>

<div class="abs value" style="left:154px;top:1005px"><div class="value-dot"><svg width="30" height="30" viewBox="0 0 30 30" fill="none" stroke="#fff" stroke-width="2"><path d="M9 5h12v7a6 6 0 01-12 0z"/><path d="M15 18v5M10 25h10M9 8H5a4 4 0 004 5M21 8h4a4 4 0 01-4 5"/></svg></div>WE'VE REPUTION<br>FOR EXCELLENCE</div>
<div class="abs value" style="left:290px;top:1005px"><div class="value-dot"><svg width="30" height="30" viewBox="0 0 30 30" fill="none" stroke="#fff" stroke-width="2"><path d="M3 11l6-3 6 4 6-4 6 3v8l-8 5-4-3-4 3-8-5z"/></svg></div>WE BUILD<br>PARTNERSHIPS</div>
<div class="abs value" style="left:424px;top:1005px"><div class="value-dot"><svg width="30" height="30" viewBox="0 0 30 30" fill="none" stroke="#fff" stroke-width="2"><path d="M6 13h5v12H6zM11 14l4-8c2 0 3 1 3 3l-1 4h7a2 2 0 012 2l-2 8a2 2 0 01-2 2H11"/></svg></div>GUIDED BY<br>COMMITMENT</div>
<div class="abs value" style="left:560px;top:1005px"><div class="value-dot"><svg width="30" height="30" viewBox="0 0 30 30" fill="none" stroke="#fff" stroke-width="2"><path d="M9 11a6 6 0 0112 0zM10 11v2a5 5 0 0010 0v-2M5 27c0-5 4-8 10-8s10 3 10 8"/></svg></div>A TEAM OF<br>PROFESSIONALS</div>

<div class="abs quote-card"></div>
<svg class="abs" style="left:739px;top:827px" width="298" height="71" viewBox="0 0 298 71"><polygon points="0,20 149,0 298,20 298,71 0,71" fill="var(--orange)"/></svg>
<div class="abs quote-card-title center">GET A QUOTE</div>
<div class="abs field" style="left:758px;top:917px;width:262px;height:34px">Name</div>
<div class="abs field" style="left:758px;top:959px;width:262px;height:34px">Email</div>
<div class="abs field" style="left:758px;top:1000px;width:262px;height:34px">Contact No.</div>
<div class="abs field" style="left:758px;top:1041px;width:262px;height:68px">Message</div>
<div class="abs btn" style="left:816px;top:1116px;width:150px;height:37px">SEND MESSAGE</div>

<!-- Stats -->
<div class="abs stats"></div>
<div class="abs stat" style="left:144px"><div class="stat-num">53</div><div class="stat-label">Total Projects</div></div>
<div class="abs stat" style="left:371px"><div class="stat-num">371</div><div class="stat-label">Staff Members</div></div>
<div class="abs stat" style="left:598px"><div class="stat-num">15</div><div class="stat-label">Working in States</div></div>
<div class="abs stat" style="left:825px"><div class="stat-num">2600</div><div class="stat-label">Hours for Work</div></div>

<!-- What we do -->
<h2 class="abs h2 center" style="left:0;top:1818px;width:1200px">WHAT WE DO</h2>
<p class="abs para center" style="left:270px;top:1873px;width:660px;font-size:11px">Lorem Ipsum is simply dummy text of the printing and typesetting industry. Lorem Ipsum has been the industry's standard dummy text ever since the 1500s</p>

<div class="abs card" style="left:161px">
  <div class="card-photo" role="img" aria-label="Photo of a worker repairing a water-damaged floor" style="background:linear-gradient(135deg,#d8d2c6,#9c8b74)"><svg class="abs" style="left:0;bottom:0" width="195" height="30" viewBox="0 0 195 30"><polygon points="0,26 195,0 195,4 0,30" fill="var(--orange)"/><polygon points="0,30 195,4 195,30" fill="var(--panel)"/></svg></div>
  <div class="card-title">Water and Fire Damage</div>
  <div class="card-text">Lorem Ipsum is simply dummy text of the printing and typesetting industry. Lorem Ipsum has been the industry.</div>
</div>
<div class="abs card" style="left:388px">
  <div class="card-photo" role="img" aria-label="Photo of a remodeled living room" style="background:linear-gradient(135deg,#e6e0d6,#a79886)"><svg class="abs" style="left:0;bottom:0" width="195" height="30" viewBox="0 0 195 30"><polygon points="0,26 195,0 195,4 0,30" fill="var(--orange)"/><polygon points="0,30 195,4 195,30" fill="var(--panel)"/></svg></div>
  <div class="card-title">Residential ReModels</div>
  <div class="card-text">Lorem Ipsum is simply dummy text of the printing and typesetting industry. Lorem Ipsum has been the industry.</div>
</div>
<div class="abs card" style="left:615px">
  <div class="card-photo" role="img" aria-label="Photo of a house with a landscaped lawn" style="background:linear-gradient(135deg,#8aa06a,#4f6b3a)"><svg class="abs" style="left:0;bottom:0" width="195" height="30" viewBox="0 0 195 30"><polygon points="0,26 195,0 195,4 0,30" fill="var(--orange)"/><polygon points="0,30 195,4 195,30" fill="var(--panel)"/></svg></div>
  <div class="card-title">Landscaping</div>
  <div class="card-text">Lorem Ipsum is simply dummy text of the printing and typesetting industry. Lorem Ipsum has been the industry.</div>
</div>
<div class="abs card" style="left:843px">
  <div class="card-photo" role="img" aria-label="Photo of a small accessory dwelling unit" style="background:linear-gradient(135deg,#9aa4a8,#4d5a60)"><svg class="abs" style="left:0;bottom:0" width="195" height="30" viewBox="0 0 195 30"><polygon points="0,26 195,0 195,4 0,30" fill="var(--orange)"/><polygon points="0,30 195,4 195,30" fill="var(--panel)"/></svg></div>
  <div class="card-title">Building ADU</div>
  <div class="card-text">Lorem Ipsum is simply dummy text of the printing and typesetting industry. Lorem Ipsum has been the industry.</div>
</div>

<!-- Recent projects -->
<div class="abs projects"></div>
<h2 class="abs h2 center" style="left:0;top:2377px;width:1200px">RECENT PROJECTS</h2>
<p class="abs para center" style="left:270px;top:2431px;width:660px;font-size:11px">Lorem Ipsum is simply dummy text of the printing and typesetting industry. Lorem Ipsum has been the industry's standard dummy text ever since the 1500s</p>
<div class="tile" role="img" aria-label="Photo of a school building" style="left:161px;top:2509px;width:210px;height:181px;background:linear-gradient(180deg,#6f98c8,#c9b79a)"></div>
<div class="tile" role="img" aria-label="Photo of a styled interior with framed prints and a green cabinet" style="left:386px;top:2509px;width:209px;height:376px;background:linear-gradient(180deg,#ececec 0%,#dcd8d2 60%,#1f7a66 75%,#186a58 100%)"></div>
<div class="tile" role="img" aria-label="Photo of a flower bed edged with white stones" style="left:611px;top:2509px;width:426px;height:181px;background:linear-gradient(180deg,#7e6a55,#b79a3a 55%,#8b7c66)"></div>
<div class="tile" role="img" aria-label="Photo of a brick family home" style="left:161px;top:2705px;width:210px;height:180px;background:linear-gradient(180deg,#3a6fc2,#b7b1aa 60%,#4f6a3c)"></div>
<div class="tile" role="img" aria-label="Rendering of a house beside a garden pond" style="left:611px;top:2705px;width:205px;height:180px;background:linear-gradient(180deg,#7fb4d8,#5f8d3e 60%,#2c7fa6)"></div>
<div class="tile" role="img" aria-label="Photo of a suburban house at dusk" style="left:832px;top:2705px;width:205px;height:180px;background:linear-gradient(180deg,#5a6e9c,#b9a7b0 55%,#6c6770)"></div>

<!-- Testimonial -->
<div class="abs testimonial"></div>
<div class="abs avatar" role="img" aria-label="Portrait of the client giving the testimonial"></div>
<div class="abs badge">“</div>
<p class="abs test-text">and for all the wonderful work you and your crew are doing. Our team has nothing but good things to say – we are really fortunate to have found you for this project!"</p>
<div class="abs test-name"><b>– Mark Ellison</b> Chairman Hollow Oak</div>
<div class="abs dot" style="left:292px"></div>
<div class="abs dot" style="left:314px;background:var(--orange)"></div>
<div class="abs dot" style="left:336px"></div>

<!-- Contact -->
<h2 class="abs h2 center" style="left:0;top:3218px;width:1200px">GET IN TOUCH WITH US</h2>
<p class="abs para center" style="left:270px;top:3272px;width:660px;font-size:11px">Lorem Ipsum is simply dummy text of the printing and typesetting industry. Lorem Ipsum has been the industry's standard dummy text ever since the 1500s</p>
<div class="abs field" style="left:292px;top:3353px;width:300px;height:36px">Name</div>
<div class="abs field" style="left:608px;top:3353px;width:299px;height:36px">Contact No.</div>
<div class="abs field" style="left:292px;top:3405px;width:615px;height:36px">Email</div>
<div class="abs field" style="left:292px;top:3458px;width:615px;height:90px">Message</div>
<div class="abs btn" style="left:526px;top:3568px;width:148px;height:36px">SEND MESSAGE</div>

<!-- Footer -->
<div class="abs footer"></div>
<div class="abs footer-brand"><span class="brand-mark" style="background:var(--orange)"></span><span class="brand-name" style="color:var(--orange)">Summit Builders</span></div>

<div class="abs ficon" style="left:161px;top:3812px"><svg width="24" height="24" viewBox="0 0 24 24" fill="none" stroke="#777" stroke-width="1.5"><path d="M12 22s7-7 7-12a7 7 0 00-14 0c0 5 7 12 7 12z"/><circle cx="12" cy="10" r="2.5"/></svg></div>
<div class="abs finfo" style="left:233px;top:3818px">1420 Ridgeview Ave Fairhaven,<br>CA 90000</div>

<div class="abs ficon" style="left:512px;top:3812px"><svg width="24" height="24" viewBox="0 0 24 24" fill="none" stroke="#777" stroke-width="1.5"><path d="M6.6 10.8a15 15 0 006.6 6.6l2.2-2.2a1 1 0 011-.25 11.4 11.4 0 003.6.6 1 1 0 011 1V20a1 1 0 01-1 1A17 17 0 013 4a1 1 0 011-1h3.5a1 1 0 011 1c0 1.25.2 2.45.6 3.6a1 1 0 01-.25 1z"/></svg></div>
<div class="abs finfo" style="left:584px;top:3818px">Direct Call<br><b>661-555-2290</b></div>

<div class="abs ficon" style="left:770px;top:3812px"><svg width="26" height="20" viewBox="0 0 26 20" fill="none" stroke="#777" stroke-width="1.5"><rect x="1" y="1" width="24" height="18"/><polyline points="1,1 13,11 25,1"/></svg></div>
<div class="abs finfo" style="left:842px;top:3818px">Email Us<br><b>hello@summitbuildersca.example</b></div>

<div class="abs social" style="left:526px"></div>
<div class="abs social" style="left:571px"></div>
<div class="abs social" style="left:615px"></div>
<div class="abs social" style="left:660px"></div>
<div class="abs copy">© SUMMIT BUILDERS – 2020. All Rights Reserved.</div>

</body>
</html>
```